Law Offices business card

Hi there, I'll need business card for the Law Offices of Colin Matheny. The information must convey his strategic approach and quick resolution to complex business litigation needs. Please emphasize Civil Litigation, Corporate Law, Business Governance and Real Estate Law. Colin has over 25 years of experience in these fields.The card should be modern and edgy and the message should be clear. Please consult his current website for ideas.

```html
<!DOCTYPE html>
<html lang="en">
<head>
<meta charset="utf-8">
<title>Law Offices of Colin Matheny – Business Card</title>
<link rel="stylesheet" href="https://fonts.googleapis.com/css2?family=Lato:wght@400;700&display=swap">
<style>
  :root {
    --backdrop: #3b3331;
    --card: #1b1b1c;
    --card-edge: #2a2a2b;
    --ink: #f2f2f2;
    --ink-soft: #c9c9c9;
    --ink-muted: #9a9a9a;
    --accent: #c9302c;
    --rule: #7a7a7a;
  }
  * { box-sizing: border-box; margin: 0; padding: 0; }
  html, body { width: 1200px; height: 814px; overflow: hidden; }
  body {
    background: var(--backdrop);
    font-family: "Lato", sans-serif;
    display: flex;
    align-items: center;
    justify-content: center;
    gap: 40px;
  }
  .card {
    width: 540px;
    height: 309px;
    background: var(--card);
    border: 1px solid var(--card-edge);
    position: relative;
    color: var(--ink);
  }

  /* Front */
  .card--front {
    display: flex;
    flex-direction: column;
    align-items: center;
    justify-content: center;
  }
  .firm-mark {
    display: flex;
    align-items: center;
    gap: 12px;
  }
  .firm-mark__square {
    width: 14px;
    height: 14px;
    background: var(--ink-soft);
    flex: none;
  }
  .firm-mark__name {
    font-weight: 700;
    font-size: 21px;
    line-height: 1.2;
    color: var(--ink-soft);
  }
  .practice {
    margin-top: 26px;
    text-align: center;
  }
  .practice__areas {
    font-size: 11px;
    letter-spacing: 0.14em;
    text-transform: uppercase;
    color: var(--ink-muted);
  }
  .practice__years {
    margin-top: 7px;
    font-size: 11px;
    font-weight: 700;
    letter-spacing: 0.14em;
    text-transform: uppercase;
    color: var(--accent);
  }
  .front-web {
    margin-top: 26px;
    font-size: 14px;
    letter-spacing: 0.42em;
    color: var(--ink-soft);
  }

  /* Back */
  .card--back {
    display: flex;
    align-items: center;
  }
  .back-brand {
    width: 270px;
    padding-left: 34px;
  }
  .back-brand .firm-mark__square { background: var(--accent); }
  .back-brand .firm-mark__name { color: var(--ink); font-size: 19px; }
  .divider {
    width: 1px;
    height: 180px;
    background: linear-gradient(to bottom, transparent, var(--rule), transparent);
  }
  .contact {
    padding-left: 24px;
    font-size: 14px;
    line-height: 1.35;
    color: var(--ink);
  }
  .contact__name {
    color: var(--accent);
    font-size: 19px;
  }
  .contact__title { font-size: 15px; margin-bottom: 14px; }
  .contact__address { margin-bottom: 6px; }
  .contact__list { list-style: none; }
  .contact__item {
    display: flex;
    align-items: center;
    gap: 9px;
    height: 20px;
  }
  .contact__icon { width: 13px; height: 13px; fill: var(--accent); flex: none; }
</style>
</head>
<body>
  <section class="card card--front" aria-label="Card front">
    <div class="firm-mark">
      <span class="firm-mark__square"></span>
      <span class="firm-mark__name">Law Offices of<br>Colin Matheny, PA</span>
    </div>
    <div class="practice">
      <p class="practice__areas">Civil Litigation · Corporate Law · Business Governance · Real Estate Law</p>
      <p class="practice__years">Over 25 Years of Experience</p>
    </div>
    <p class="front-web">WWW.MATHENYLAW.COM</p>
  </section>

  <section class="card card--back" aria-label="Card back">
    <div class="back-brand">
      <div class="firm-mark">
        <span class="firm-mark__square"></span>
        <span class="firm-mark__name">Law Offices of<br>Colin Matheny, PA</span>
      </div>
    </div>
    <div class="divider"></div>
    <div class="contact">
      <p class="contact__name">Colin Matheny</p>
      <p class="contact__title">Attorney</p>
      <p class="contact__address">318B Harbor Lane<br>Coral Point, Florida 33412</p>
      <ul class="contact__list">
        <li class="contact__item">
          <svg class="contact__icon" viewBox="0 0 16 16" aria-hidden="true"><path d="M3.5 1l3 3-1.6 1.8a9 9 0 0 0 5.3 5.3L12 9.5l3 3-2 2.2C7 14.5 1.5 9 1.3 3z"/></svg>
          <span>555-214-7380</span>
        </li>
        <li class="contact__item">
          <svg class="contact__icon" viewBox="0 0 16 16" aria-hidden="true"><rect x="4" y="1" width="8" height="4"/><rect x="1" y="6" width="14" height="6" rx="1"/><rect x="4" y="10" width="8" height="5"/></svg>
          <span>555-214-7391</span>
        </li>
        <li class="contact__item">
          <svg class="contact__icon" viewBox="0 0 16 16" aria-hidden="true"><path d="M1 3h14v10H1z M1 3l7 6 7-6" stroke="#1b1b1c" stroke-width="1.2"/></svg>
          <span>colin@mathenylaw.com</span>
        </li>
        <li class="contact__item">
          <svg class="contact__icon" viewBox="0 0 16 16" aria-hidden="true"><circle cx="8" cy="8" r="7"/><path d="M1 8h14M8 1c-3 3.5-3 10.5 0 14M8 1c3 3.5 3 10.5 0 14" stroke="#1b1b1c" stroke-width="1" fill="none"/></svg>
          <span>www.mathenylaw.com</span>
        </li>
      </ul>
    </div>
  </section>
</body>
</html>
```